Software Development Consulting Company Needs Business Card Design

We need a new business card design for our consultants at Kestrel Works (kestrelworks.example). We are a small firm that provides high-end software development and methodology consulting to medium to large enterprise IT organizations.

Our logo uses Futura for the font and we would like to stick with navy blue and canary yellow for the logo colors. Attached are normal and reversed versions of our logos in illustrator format.
Updates

Hi Everyone, Thank yo very much for your amazing design ideas. I have created a poll for this project and our employees will be voting on the design they wish to use. We will be making a decision this Wednesday (October 22nd). Thanks again, Dale Hartwick

Industry/Entity Type

Business

```html
<!DOCTYPE html>
<html lang="en">
<head>
<meta charset="utf-8">
<title>Kestrel Works – Business Card</title>
<link rel="stylesheet" href="https://fonts.googleapis.com/css2?family=Jost:wght@400;500;600&family=Mulish:wght@400;600;700&display=swap">
<style>
  :root {
    --navy: #1f4166;
    --canary: #ffec00;
    --paper: #ffffff;
    --ink: #3a3d45;
    --muted: #5b5e66;
    --stage: #ecebe8;
  }
  * { box-sizing: border-box; margin: 0; padding: 0; }
  html, body {
    width: 1200px; height: 720px; overflow: hidden;
    background: var(--stage);
  }
  .sheet {
    width: 1200px; height: 720px;
    display: flex; align-items: center; justify-content: center; gap: 40px;
  }
  .card {
    width: 520px; height: 297px;
    position: relative;
    box-shadow: 0 2px 8px rgba(0,0,0,.12);
  }
  .card--front { background: var(--paper); }
  .card--back { background: var(--canary); }

  /* logotype */
  .wordmark {
    display: flex; align-items: center; justify-content: center; gap: 12px;
    font-family: "Jost", sans-serif; font-weight: 500;
    color: var(--navy); letter-spacing: .14em; text-transform: uppercase;
  }
  .wordmark__dot {
    border: 3px solid var(--navy); border-radius: 50%;
    flex: none;
  }
  .card--front .wordmark { position: absolute; top: 52px; left: 0; right: 0; font-size: 30px; }
  .card--front .wordmark__dot { width: 30px; height: 30px; }

  .holder {
    position: absolute; top: 138px; left: 0; right: 0; text-align: center;
    font-family: "Mulish", sans-serif; font-size: 16px; color: var(--navy);
  }
  .holder__name { font-weight: 700; }
  .holder__title { font-weight: 400; font-size: 13px; color: var(--ink); }

  .contact {
    position: absolute; top: 178px; left: 0; right: 0;
    display: flex; justify-content: center; gap: 28px;
    font-family: "Mulish", sans-serif; font-size: 12.5px; color: var(--ink);
  }
  .contact__col { display: flex; flex-direction: column; gap: 5px; }
  .contact__item { display: flex; align-items: center; gap: 6px; white-space: nowrap; }
  .contact__item--plain { padding-left: 18px; }
  .contact__icon { width: 12px; height: 12px; flex: none; fill: none; stroke: var(--navy); stroke-width: 1.6; }

  .card--back .wordmark {
    position: absolute; top: 92px; left: 0; right: 0;
    flex-direction: column; gap: 14px; font-size: 24px;
  }
  .card--back .wordmark__dot { width: 54px; height: 54px; border-width: 5px; }
  .site {
    position: absolute; bottom: 42px; left: 0; right: 0; text-align: center;
    font-family: "Mulish", sans-serif; font-size: 15px; letter-spacing: .22em;
    color: var(--muted);
  }
</style>
</head>
<body>
<main class="sheet">
  <section class="card card--front" aria-label="Card front">
    <div class="wordmark"><span class="wordmark__dot"></span>Kestrel Works</div>
    <p class="holder"><span class="holder__name">Your Name,</span> <span class="holder__title">Title</span></p>
    <div class="contact">
      <div class="contact__col">
        <span class="contact__item">
          <svg class="contact__icon" viewBox="0 0 12 12"><path d="M3 1.5 L4.6 3.6 L3.7 4.6 Q4.8 7 7.4 8.3 L8.4 7.4 L10.5 9 L9.4 10.6 Q5.5 10.2 2.5 6.8 Q1.2 4.8 1.5 2.6 Z"/></svg>
          012-345-6789
        </span>
      </div>
      <div class="contact__col">
        <span class="contact__item">
          <svg class="contact__icon" viewBox="0 0 12 12"><rect x="1" y="2.5" width="10" height="7"/><path d="M1 2.5 L6 6.5 L11 2.5"/></svg>
          info@kestrelworks.example
        </span>
        <span class="contact__item">
          <svg class="contact__icon" viewBox="0 0 12 12"><circle cx="6" cy="6" r="5"/><ellipse cx="6" cy="6" rx="2.2" ry="5"/><path d="M1 6 H11"/></svg>
          www.kestrelworks.example
        </span>
        <span class="contact__item contact__item--plain">Harborton + Lindenvale, ST</span>
      </div>
    </div>
  </section>

  <section class="card card--back" aria-label="Card back">
    <div class="wordmark"><span class="wordmark__dot"></span>Kestrel Works</div>
    <p class="site">www.kestrelworks.example</p>
  </section>
</main>
</body>
</html>
```